Commercial Swimming Pool - Design-Build Contractor Website Design

I need a new website that will feature our newly developed logo and trade name as well as provide a fully updated site experience. We are not a residential builder - we strictly design and install high-end commercial pools. I need the website to highlight our portfolio and communicate the various types of projects in which we specialize. I want the effect of the site to reflect the high-end nature of our services - projects like the 57th floor spa at the Phila Silver Willow, the aquatic therapy portion of the Phila Ravenhawks training facility, a 5om indoor competition pool for the prestigious Dallowmere Academy, the indoor water park at The Quenwick Lodge or the recent country club renovation projects we've completed in our region (to name a few examples).
Need extra days to review

```html
<!DOCTYPE html>
<html lang="en">
<head>
<meta charset="utf-8">
<title>Corwell Aquatics — Commercial Pool Design-Build</title>
<link rel="stylesheet" href="https://fonts.googleapis.com/css2?family=Lato:ital,wght@0,400;0,700;0,900;1,700;1,900&display=swap">
<style>
:root{
  --navy:#0f2a4a;
  --ink:#1c1f24;
  --muted:#5b6470;
  --sky:#3aa9e2;
  --sky-deep:#2285c9;
  --btn:#2f8fd8;
  --btn-dark:#1c5fa3;
  --line:#d5dbe2;
  --white:#ffffff;
  --black:#050505;
  --star:#f6b52a;
}
*{box-sizing:border-box;margin:0;padding:0}
html,body{width:1200px;height:3620px;overflow:hidden}
body{font-family:"Lato",Arial,sans-serif;color:var(--ink);background:var(--white);position:relative}
.photo{position:absolute;display:block}
.btn{display:inline-block;background:linear-gradient(90deg,var(--btn),var(--btn-dark));color:var(--white);font-weight:700;font-size:15px;padding:12px 26px;border-radius:3px}
.brand{display:flex;align-items:center;gap:10px;font-weight:900;font-size:22px;color:var(--navy);letter-spacing:.5px}
.brand .dot{width:34px;height:34px;border-radius:50%;background:var(--sky)}
.section-title{font-style:italic;font-weight:900;font-size:36px;text-align:center}

/* header */
.site-header{position:absolute;top:0;left:0;width:1200px;height:64px;background:rgba(255,255,255,.96);display:flex;align-items:center;justify-content:space-between;padding:0 40px 0 60px;z-index:3}
.nav{display:flex;gap:32px;align-items:center;font-weight:700;font-size:15px;color:var(--navy)}
.nav .cta{background:var(--btn);color:var(--white);padding:9px 16px;border-radius:3px}

/* hero */
.hero{position:absolute;top:0;left:0;width:1200px;height:620px;overflow:hidden}
.hero-bg{top:0;left:0;width:1200px;height:620px;background:linear-gradient(160deg,#b9c9d6 0%,#7f9ab3 30%,#3b77a3 58%,#1b8fc8 78%,#0b4f7f 100%)}
.hero-shade{position:absolute;inset:0;background:linear-gradient(90deg,rgba(8,25,45,.6),rgba(8,25,45,.1) 60%)}
.hero-copy{position:absolute;left:108px;top:170px;width:440px;color:var(--white)}
.hero-copy h1{font-style:italic;font-weight:900;font-size:62px;line-height:1.02;text-transform:uppercase}
.hero-copy p{font-size:14px;line-height:1.6;margin:20px 0 30px;width:330px}
.hero-wave{position:absolute;left:0;bottom:0}

/* about */
.about{position:absolute;top:620px;left:0;width:1200px;height:620px}
.about-photo{left:140px;top:80px;width:290px;height:290px;border-radius:50%;background:radial-gradient(circle at 40% 30%,#e7dccb 0%,#b9a58b 40%,#3d9fcf 70%,#1f6fa7 100%)}
.about-mark{position:absolute;border-radius:50%;background:var(--white);box-shadow:0 2px 8px rgba(0,0,0,.15);display:flex;align-items:center;justify-content:center}
.about-mark span{width:60%;height:60%;border-radius:50%;background:var(--sky)}
.about-copy{position:absolute;left:598px;top:108px;width:490px}
.about-copy h2{font-style:italic;font-weight:900;font-size:38px;margin-bottom:16px}
.about-copy p{font-size:13px;line-height:1.6;color:var(--ink)}
.about-copy .btn{margin-top:24px}

/* projects */
.projects{position:absolute;top:1240px;left:0;width:1200px;height:500px;background:linear-gradient(180deg,#55b8e8,var(--sky) 50%,#5cbbe6)}
.projects .section-title{color:var(--white);position:absolute;top:52px;width:100%}
.card{position:absolute;top:122px;height:310px;overflow:hidden}
.card .photo{inset:0}
.card-caption{position:absolute;left:40px;bottom:60px;color:var(--white);font-weight:700;font-size:19px;line-height:1.35;width:220px}
.card-shade{position:absolute;inset:0;background:linear-gradient(0deg,rgba(0,0,0,.55),transparent 55%)}
.arrow{position:absolute;top:270px}

/* portfolio */
.portfolio{position:absolute;top:1740px;left:0;width:1200px;height:600px}
.portfolio .section-title{position:absolute;top:0;width:100%}

/* testimonials */
.testimonials{position:absolute;top:2340px;left:0;width:1200px;height:540px;overflow:hidden}
.testimonials-bg{inset:0;background:linear-gradient(180deg,#6fc4ec,#3aa9e2 40%,#53b6e6)}
.testimonials .section-title{color:var(--white);position:absolute;top:60px;width:100%}
.quote-card{position:absolute;top:150px;width:294px;height:310px;background:var(--white);border-radius:4px;padding:22px 20px}
.quote-head{display:flex;align-items:center;gap:12px;margin-bottom:16px}
.quote-card p{font-size:13.5px;line-height:1.6}
.quote-by{margin-top:14px;font-size:12px}
.quote-by b{font-weight:700}
.stars{display:flex;gap:3px}

/* call back */
.callback{position:absolute;top:2880px;left:0;width:1200px;height:480px}
.callback .section-title{position:absolute;top:40px;width:100%;font-size:34px}
.field{position:absolute;border:1px solid var(--line);border-radius:3px;padding:6px 10px}
.field label{display:block;font-size:12px;color:var(--ink);margin-bottom:4px}
.field span{font-size:12px;color:#9aa3ad}
.field.active{border-color:var(--sky)}
.consent{position:absolute;left:110px;top:403px;display:flex;gap:14px;width:800px}
.consent i{width:16px;height:16px;border:1px solid var(--line);flex:none;margin-top:4px}
.consent p{font-size:12px;color:var(--muted);line-height:1.6}
.submit{position:absolute;left:920px;top:405px;padding:10px 24px}

/* footer */
.site-footer{position:absolute;top:3360px;left:0;width:1200px;height:260px;background:var(--black);color:var(--white);text-align:center}
.site-footer .brand{color:var(--white);justify-content:center;margin-top:58px;font-size:28px}
.footer-nav{display:flex;justify-content:center;gap:38px;margin-top:28px;font-size:14px;font-weight:700}
.socials{display:flex;justify-content:center;gap:18px;margin-top:22px}
.socials span{width:34px;height:34px;border-radius:50%;border:1.5px solid var(--white)}
.copyright{position:absolute;bottom:14px;width:100%;font-size:12px;color:#cfd3d8}
.call-tag{position:absolute;right:10px;bottom:14px;font-size:12px;color:#cfd3d8}
</style>
</head>
<body>

<header class="site-header">
  <div class="brand"><span class="dot"></span>CORWELL AQUATICS</div>
  <nav class="nav">
    <span>About Us</span><span>Services</span><span>Portfolio</span><span>Projects</span><span class="cta">Contact Us</span>
  </nav>
</header>

<section class="hero">
  <div class="photo hero-bg" role="img" aria-label="Resort courtyard with a large blue commercial pool, lounge chairs and a small arched bridge"></div>
  <div class="hero-shade"></div>
  <div class="hero-copy">
    <h1>Welcome to Corwell Aquatics</h1>
    <p>We design and build high-end commercial pools, spas and aquatic facilities for hotels, schools and clubs.</p>
    <span class="btn">Read More</span>
  </div>
  <svg class="hero-wave" width="1200" height="90" viewBox="0 0 1200 90" aria-hidden="true">
    <path d="M0 60 Q600 110 1200 20 L1200 90 L0 90 Z" fill="#ffffff"/>
    <path d="M0 55 Q600 100 1200 14" fill="none" stroke="#1c5fa3" stroke-width="6"/>
  </svg>
</section>

<section class="about">
  <div class="photo about-photo" role="img" aria-label="Apartment complex rising behind a rectangular outdoor pool"></div>
  <div class="about-mark" style="left:118px;top:72px;width:70px;height:70px"><span></span></div>
  <div class="about-mark" style="left:370px;top:312px;width:78px;height:78px"><span></span></div>
  <div class="about-copy">
    <h2>About Us</h2>
    <p>For over twenty years our team has designed and installed commercial pools for hotels, universities, clubs and wellness centers. We handle every phase, from early concept and engineering to construction, finishes and final commissioning, so owners work with one accountable partner.</p>
    <p>Our portfolio includes rooftop spas, competition natatoriums, therapy pools and indoor water parks. Each project is built to high standards of safety, efficiency and craftsmanship, and we stay involved long after opening day.</p>
    <span class="btn">Read More</span>
  </div>
</section>

<section class="projects">
  <svg style="position:absolute;top:-1px;left:0" width="1200" height="40" viewBox="0 0 1200 40" aria-hidden="true"><path d="M0 0 L1200 0 L1200 6 Q600 40 0 10 Z" fill="#ffffff"/></svg>
  <h2 class="section-title">Our Projects</h2>
  <div class="card" style="left:80px;width:318px">
    <div class="photo" role="img" aria-label="Rooftop spa pool at dusk with city skyline" style="background:linear-gradient(160deg,#1d3f5d,#2f6c8f 45%,#0f7fb5 70%,#0c3552)"></div>
    <div class="card-shade"></div>
    <div class="card-caption">57th floor spa at the Phila Silver Willow</div>
    <svg style="position:absolute;right:22px;bottom:22px" width="26" height="26" viewBox="0 0 26 26" aria-hidden="true"><path d="M4 22 L22 4 M10 4 H22 V16" stroke="#fff" stroke-width="3" fill="none"/></svg>
  </div>
  <div class="card" style="left:436px;width:296px">
    <div class="photo" role="img" aria-label="Palm-lined resort pool under a bright sky" style="background:linear-gradient(180deg,#e9e2cf,#d0b07a 35%,#5a8a62 55%,#1fa4d8 80%,#2b6f99)"></div>
  </div>
  <div class="card" style="left:790px;width:318px">
    <div class="photo" role="img" aria-label="Spanish-style hotel courtyard with pool and palm trees" style="background:linear-gradient(180deg,#8ec7ea,#d7b58a 35%,#9b6b44 55%,#2fa8d6 80%,#1f6d9d)"></div>
  </div>
  <svg class="arrow" style="left:14px" width="20" height="30" viewBox="0 0 20 30" aria-hidden="true"><path d="M16 3 L4 15 L16 27" stroke="#fff" stroke-width="4" fill="none"/></svg>
  <svg class="arrow" style="right:14px" width="20" height="30" viewBox="0 0 20 30" aria-hidden="true"><path d="M4 3 L16 15 L4 27" stroke="#fff" stroke-width="4" fill="none"/></svg>
</section>

<section class="portfolio">
  <h2 class="section-title" style="top:38px">Portfolio</h2>
  <div class="photo" role="img" aria-label="Tower building lit at dusk above a resort pool" style="left:108px;top:38px;width:296px;height:490px;top:40px;background:linear-gradient(180deg,#3c5e86,#7e8fa8 35%,#c7a97a 60%,#27a2c9 85%,#0f4f72)"></div>
  <div class="photo" role="img" aria-label="Lanes of an indoor competition pool seen from above" style="left:448px;top:40px;width:292px;height:222px;background:linear-gradient(135deg,#2bb3e8,#0c7cc4 50%,#1aa0de)"></div>
  <div class="photo" role="img" aria-label="Resort pool with palm trees at twilight" style="left:788px;top:40px;width:294px;height:222px;background:linear-gradient(180deg,#5b87b6,#c6a06d 45%,#2e7a5e 65%,#2aa4d2)"></div>
  <div class="photo" role="img" aria-label="Wide view of a hotel pool and lit facade at night" style="left:448px;top:300px;width:634px;height:230px;background:linear-gradient(180deg,#23416a,#6f7d99 35%,#d7b27a 55%,#2aa8d3 80%,#0c4b6e)"></div>
</section>

<section class="testimonials">
  <div class="photo testimonials-bg" role="img" aria-label="Faded blue view of a building beside a pool"></div>
  <h2 class="section-title">Testimonials</h2>
  <div class="quote-card" style="left:108px">
    <div class="quote-head">
      <svg width="34" height="26" viewBox="0 0 34 26" aria-hidden="true"><path d="M2 26 V14 Q2 2 14 0 V6 Q8 8 8 14 H14 V26 Z M20 26 V14 Q20 2 32 0 V6 Q26 8 26 14 H32 V26 Z" fill="#c9cdd2"/></svg>
      <div class="stars"><svg width="110" height="20" viewBox="0 0 110 20" aria-hidden="true"><g fill="#f6b52a"><path id="st" d="M10 1 L12.6 7 L19 7.3 L14 11.4 L15.8 18 L10 14.3 L4.2 18 L6 11.4 L1 7.3 L7.4 7 Z"/><use href="#st" x="22"/><use href="#st" x="44"/><use href="#st" x="66"/><use href="#st" x="88"/></g></svg></div>
    </div>
    <p>"The team delivered our new natatorium on schedule and within budget. Their attention to detail in the tile work, filtration and lighting is clear every day our swimmers use it."</p>
    <div class="quote-by"><b>-Jonathan</b> &nbsp;CEO Company</div>
  </div>
  <div class="quote-card" style="left:450px">
    <div class="quote-head">
      <svg width="34" height="26" viewBox="0 0 34 26" aria-hidden="true"><path d="M2 26 V14 Q2 2 14 0 V6 Q8 8 8 14 H14 V26 Z M20 26 V14 Q20 2 32 0 V6 Q26 8 26 14 H32 V26 Z" fill="#c9cdd2"/></svg>
      <svg width="110" height="20" viewBox="0 0 110 20" aria-hidden="true"><g fill="#f6b52a"><use href="#st"/><use href="#st" x="22"/><use href="#st" x="44"/><use href="#st" x="66"/><use href="#st" x="88"/></g></svg>
    </div>
    <p>"From the first sketches to opening weekend, they managed every detail of our club renovation. Members love the new pool deck and the spa, and the project ran smoothly throughout."</p>
    <div class="quote-by"><b>-Richard</b> &nbsp;CEO Company</div>
  </div>
  <div class="quote-card" style="left:792px">
    <div class="quote-head">
      <svg width="34" height="26" viewBox="0 0 34 26" aria-hidden="true"><path d="M2 26 V14 Q2 2 14 0 V6 Q8 8 8 14 H14 V26 Z M20 26 V14 Q20 2 32 0 V6 Q26 8 26 14 H32 V26 Z" fill="#c9cdd2"/></svg>
      <svg width="110" height="20" viewBox="0 0 110 20" aria-hidden="true"><g fill="#f6b52a"><use href="#st"/><use href="#st" x="22"/><use href="#st" x="44"/><use href="#st" x="66"/><use href="#st" x="88"/></g></svg>
    </div>
    <p>"Our therapy pool was a complex build with strict requirements. They brought clear answers, skilled crews and steady communication, and the finished facility exceeded our expectations."</p>
    <div class="quote-by"><b>-Jim</b> &nbsp;CEO Company</div>
  </div>
  <svg class="arrow" style="left:14px;top:290px" width="20" height="30" viewBox="0 0 20 30" aria-hidden="true"><path d="M16 3 L4 15 L16 27" stroke="#fff" stroke-width="4" fill="none"/></svg>
  <svg class="arrow" style="right:14px;top:290px" width="20" height="30" viewBox="0 0 20 30" aria-hidden="true"><path d="M4 3 L16 15 L4 27" stroke="#fff" stroke-width="4" fill="none"/></svg>
</section>

<section class="callback">
  <h2 class="section-title">Request A Call Back</h2>
  <div class="field active" style="left:110px;top:130px;width:470px;height:50px"><label>First Name</label><span>Jason</span></div>
  <div class="field" style="left:620px;top:130px;width:470px;height:50px"><label>Last Name</label><span>Smith</span></div>
  <div class="field" style="left:110px;top:200px;width:470px;height:50px"><label>Email Address</label><span>hello@example.com</span></div>
  <div class="field" style="left:620px;top:200px;width:470px;height:50px"><label>Phone No</label><span>+1 555 010 0000</span></div>
  <div class="field" style="left:110px;top:270px;width:980px;height:80px"><label>Your Message</label><span>Type Here</span></div>
  <div class="consent"><i></i><p>I agree that Corwell Aquatics may contact me by phone or email about my project request. My details will only be used to respond to this enquiry and will never be shared.</p></div>
  <span class="btn submit">Submit</span>
</section>

<footer class="site-footer">
  <div class="brand"><span class="dot"></span>CORWELL AQUATICS</div>
  <nav class="footer-nav"><span>About Us</span><span>Services</span><span>Portfolio</span><span>Projects</span><span>Contact Us</span></nav>
  <div class="socials"><span></span><span></span><span></span></div>
  <p class="copyright">2023 © Corwell Aquatics | All Rights Reserved</p>
  <span class="call-tag">Call</span>
</footer>

</body>
</html>
```